Web Design for a Biotech Consulting Firm

We need a web site design for a new business based in Philadelphia called Verantel Dx. This is a consulting firm that will serve medical diagnostics industry, which is part of the life science/healthcare industry focusing on developing and marketing products that help in early detection, monitoring or management of diseases. Our consulting firm will help medical diagnostic companies to overcome key challenges in designing, evaluating and marketing new products.Our company name is Verantel Dx. Verantel is Latin word for "something" Dx represents diagnostics. The idea behind the name is that we help companies to transform the original, early product ideas ("nothing") into "something"; which is a product with full clinical utility that will help to improve health and well-being.The web site should use the visual feel of the logo (attached), be modern, simple and clean looking and represent creativity, innovation, scientific thinking and progress.
Updates

Wix Design is acceptable

Industry/Entity Type

Orbalis

Coding

Coded - Design and coding required

Number of Pages Required

1 page

Font styles to use
Sans Serif

Requirements
Must have
• simple, clean look couple of pages
Should not have
• a lot of pages

```html
<!DOCTYPE html>
<html lang="en">
<head>
<meta charset="utf-8">
<title>Verantel Dx — Biotech Consulting</title>
<link href="https://fonts.googleapis.com/css2?family=Montserrat:wght@400;500;600;700&family=Lato:wght@400;700&display=swap" rel="stylesheet">
<style>
:root{
  --blue:#2f86ee;
  --ink:#1b1b1b;
  --text:#2a2a2a;
  --dark:#121314;
  --white:#fff;
}
*{margin:0;padding:0;box-sizing:border-box}
html,body{width:1200px;height:3019px;overflow:hidden;background:#fff}
body{position:relative;font-family:'Lato',sans-serif;color:var(--text)}
.abs{position:absolute}
/* header */
.site-header{position:absolute;left:0;top:0;width:1200px;height:110px;background:#fff}
.logo{left:115px;top:38px;display:flex;align-items:center;gap:9px;font-family:'Montserrat',sans-serif;font-weight:500;font-size:19px;color:var(--ink);white-space:nowrap}
.logo i{display:block;width:12px;height:12px;background:var(--blue)}
.nav a{position:absolute;top:53px;font-family:'Montserrat',sans-serif;font-size:14px;color:var(--ink);text-decoration:none}
.nav a.active{color:var(--blue);border:1px solid var(--blue);padding:3px 7px;top:48px}
.divider-v{left:897px;top:22px;width:1px;height:68px;background:#e3e3e3}
.call{left:935px;top:30px;width:152px;text-align:center;font-family:'Montserrat',sans-serif;font-size:17px;letter-spacing:1.5px;color:var(--ink);border-bottom:2px solid #333;padding-bottom:4px}
.phone{left:935px;top:60px;width:152px;text-align:center;font-family:'Montserrat',sans-serif;font-weight:700;font-size:21px;color:var(--blue)}
/* hero */
.hero{left:0;top:110px;width:1200px;height:563px;background:radial-gradient(ellipse at 80% 45%,#1b8de0 0%,#6fb3e2 35%,#b5d3e6 70%,#d3e2ec 100%)}
.hero h1{position:absolute;left:115px;top:172px;font-family:'Montserrat',sans-serif;font-weight:700;font-size:34px;line-height:43px;color:#111}
.arrow-btn{position:absolute;top:322px;width:28px;height:28px;border:1px solid #333;display:flex;align-items:center;justify-content:center}
.arrow-btn.alt{border-color:var(--blue)}
/* section titles */
.title{position:absolute;left:0;width:1200px;text-align:center;font-family:'Montserrat',sans-serif;font-weight:400;font-size:32px;color:var(--ink)}
.title em{font-style:normal;color:var(--blue)}
.rule{position:absolute;left:534px;width:132px;height:3px;background:linear-gradient(90deg,#222 50%,var(--blue) 50%)}
.center{position:absolute;left:0;width:1200px;text-align:center}
.welcome-sub{font-size:14.5px;line-height:23px;color:var(--blue)}
.welcome-body{font-size:13px;line-height:23px;color:#222}
.mv-icon{width:67px;height:66px;border:2px solid var(--blue);display:flex;align-items:center;justify-content:center}
.mv h3{font-family:'Montserrat',sans-serif;font-weight:600;font-size:17px;color:#111}
.mv p{font-size:13px;line-height:22px;margin-top:7px;color:#222}
.mv p a{color:var(--blue);text-decoration:none}
/* services */
.services{left:0;top:1138px;width:1200px;height:543px;background:linear-gradient(135deg,#3d8ff0,#3b8aee 60%,#3d91f2)}
.svc{position:absolute;top:225px;width:300px;text-align:center;color:#fff}
.svc .ico{height:76px;display:flex;align-items:flex-end;justify-content:center}
.svc h3{font-family:'Montserrat',sans-serif;font-weight:700;font-size:20px;margin-top:20px;letter-spacing:.3px}
.svc p{font-size:13.5px;line-height:22px;margin-top:16px;color:#eaf3ff}
.btn-outline{display:inline-block;margin-top:24px;border:1px solid #fff;padding:8px 14px;font-family:'Montserrat',sans-serif;font-size:15px;color:#fff;letter-spacing:.3px}
/* news */
.news{position:absolute;top:1846px;width:320px}
.tag{display:inline-block;background:var(--blue);color:#fff;font-family:'Montserrat',sans-serif;font-size:12.5px;padding:6px 11px}
.news h4{font-family:'Montserrat',sans-serif;font-weight:700;font-size:14.5px;margin-top:18px;color:#111;white-space:nowrap}
.news p{font-size:13.5px;line-height:22px;margin-top:8px;color:#222;width:290px}
.news a{display:block;margin-top:12px;font-size:12px;color:var(--blue);font-weight:700;text-decoration:underline}
.chev{font-size:40px;color:#999;line-height:1}
/* cta */
.cta{left:0;top:2096px;width:1200px;height:263px;background:linear-gradient(90deg,#2b2c2e,#35373a 45%,#26272a)}
.cta h2{position:absolute;left:115px;top:80px;font-family:'Montserrat',sans-serif;font-weight:700;font-size:34px;color:#fff}
.cta p{position:absolute;left:115px;top:134px;font-size:15px;line-height:24px;color:#eee}
.cta .go{position:absolute;left:876px;top:105px;width:192px;height:52px;border:2px solid #fff;display:flex;align-items:center;justify-content:center;font-family:'Montserrat',sans-serif;font-weight:700;font-size:19px;letter-spacing:1px;color:#fff}
/* partners */
.partner{position:absolute;top:2539px;width:141px;height:66px;border:1px solid #ddd;display:flex;align-items:center;justify-content:center;gap:6px;font-size:17px;color:#555}
.partner.active{border-color:var(--blue)}
.partner i{display:block;width:12px;height:12px;border-radius:50%;background:#8a8a8a}
/* footer */
.footer{left:0;top:2690px;width:1200px;height:300px;background:var(--dark);color:#fff}
.footer h5{position:absolute;top:55px;font-family:'Montserrat',sans-serif;font-weight:400;font-size:17px;letter-spacing:.3px}
.footer .ul{position:absolute;top:86px;width:44px;height:2px;background:var(--blue)}
.vsep{position:absolute;top:85px;width:1px;height:160px;background:#2a2b2d}
.links li{list-style:none;font-size:12.5px;margin-bottom:18px;position:relative;padding-left:12px}
.links li::before{content:"";position:absolute;left:0;top:6px;width:4px;height:4px;border-radius:50%;background:var(--blue)}
.contact-row{position:absolute;left:325px;display:flex;gap:14px;font-size:12.5px;line-height:17px}
.field{position:absolute;left:641px;width:225px;height:28px;background:#fff;border:1px solid #ccc;font-size:10.5px;color:#888;padding:8px 9px}
.submit{position:absolute;left:641px;top:220px;width:105px;height:29px;background:var(--blue);display:flex;align-items:center;justify-content:center;font-size:13px;font-weight:700}
.social{position:absolute;left:979px;display:flex;align-items:center;gap:9px;font-family:'Montserrat',sans-serif;font-size:12px;font-weight:500}
.social i{display:block;width:27px;height:27px;border:1px solid #ccc}
.copy{left:0;top:2990px;width:1200px;height:29px;background:var(--blue);color:#fff;font-size:11px;display:flex;align-items:center;justify-content:center}
</style>
</head>
<body>

<header class="site-header">
  <div class="abs logo"><i></i>Verantel Dx</div>
  <nav class="nav">
    <a class="active" style="left:429px">Home</a>
    <a style="left:539px">About Us</a>
    <a style="left:666px">Services</a>
    <a style="left:787px">Contact Us</a>
  </nav>
  <div class="abs divider-v"></div>
  <div class="abs call">Call Us Today</div>
  <div class="abs phone">215-555-0147</div>
</header>

<section class="abs hero" role="img" aria-label="Glowing blue DNA double helix over a soft blue laboratory background">
  <h1>We Are A Biotech Consulting<br>Firm Serving The Medical<br>Diagnostics Industry</h1>
  <div class="arrow-btn" style="left:113px"><svg width="10" height="12" viewBox="0 0 10 12"><path d="M7 1 2 6l5 5" fill="none" stroke="#222" stroke-width="2"/></svg></div>
  <div class="arrow-btn alt" style="left:151px"><svg width="10" height="12" viewBox="0 0 10 12"><path d="M3 1l5 5-5 5" fill="none" stroke="#222" stroke-width="2"/></svg></div>
</section>

<h2 class="title" style="top:748px">Welcome To Verantel <em>Dx</em></h2>
<div class="rule" style="top:796px"></div>
<p class="center welcome-sub" style="top:822px">Verantel Dx This Is A Consulting Firm That Will Serve Medical Diagnostics Industry,<br>Which Is Part of The Life Science/healthcare Industry</p>
<p class="center welcome-body" style="top:881px;left:150px;width:900px">Lorem ipsum dolor sit amet, consectetuer adipiscing elit, sed diam nonummy nibh euismod tincidunt ut laoreet dolore magna aliquam erat volutpat. Ut wisi enim ad minim veniam, quis nostrud exerci tation ullamcorper suscipit lobortis nisl ut aliquip ex ea commodo consequat. Duis autem vel eum iriure or sit amet, consectetuer adipiscing elit, sed diam nonummy nibh euismod tincidunt ut laoreet dolore magna aliquam erat volutpat. Ut wisi enim</p>

<div class="abs mv" style="left:182px;top:989px;display:flex;gap:14px">
  <div class="mv-icon"><svg width="44" height="40" viewBox="0 0 44 40"><path d="M3 37 22 10l19 27Z" fill="none" stroke="#222" stroke-width="2"/><path d="M22 10V2h9l-3 3 3 3h-9" fill="none" stroke="#222" stroke-width="2"/></svg></div>
  <div><h3>MISSION</h3><p>Lorem ipsum dolor sit amet, consectetuer adipisci<br>laoreet dolore magna aliquam erat volutpat....<a>(+)</a></p></div>
</div>
<div class="abs mv" style="left:638px;top:989px;display:flex;gap:14px">
  <div class="mv-icon"><svg width="44" height="42" viewBox="0 0 44 42"><path d="M8 30 30 12l5 6-22 17Z" fill="none" stroke="#222" stroke-width="2"/><path d="M18 30l-6 10M22 28l4 12" stroke="#222" stroke-width="2"/><circle cx="10" cy="8" r="2" fill="#222"/><circle cx="36" cy="5" r="1.5" fill="#222"/></svg></div>
  <div><h3>VISION</h3><p>Lorem ipsum dolor sit amet, consectetuer adipisci<br>laoreet dolore magna aliquam erat volutpat....<a>(+)</a></p></div>
</div>

<section class="abs services" role="img" aria-label="Blue tinted photo of a hand writing with a pen behind the services">
  <h2 class="title" style="top:76px">Our <em style="color:#fff">Services</em></h2>
  <div class="rule" style="top:124px;background:linear-gradient(90deg,#1b1b1b 50%,#9dc6f7 50%)"></div>
  <p class="center" style="top:153px;font-size:15.5px;color:#fff">Our Consulting Firm Will Help Medical Diagnostic Companies To Overcome Key Challenges In</p>

  <div class="svc" style="left:88px">
    <div class="ico"><svg width="66" height="70" viewBox="0 0 66 70" fill="none" stroke="#fff" stroke-width="2.4"><rect x="4" y="14" width="58" height="48"/><path d="M14 10v46M26 4v52M38 8v48M50 12v44M2 64h62"/></svg></div>
    <h3>Designing</h3>
    <p>Lorem ipsum dolor sit amet, consectetuer<br>adipiscing elit , sed diam nonummy nibh</p>
    <span class="btn-outline">READ MORE</span>
  </div>
  <div class="svc" style="left:441px">
    <div class="ico"><svg width="78" height="76" viewBox="0 0 78 76" fill="none" stroke="#fff" stroke-width="2.4"><rect x="4" y="8" width="48" height="64"/><path d="M18 4h20v8H18zM11 26h8v8h-8zM11 42h8v8h-8zM11 58h8v8h-8z"/><circle cx="40" cy="36" r="12"/><path d="m49 45 14 14M34 36l4 4 8-8M70 4l3 3-3 3-3-3z"/></svg></div>
    <h3>Evaluating</h3>
    <p>Lorem ipsum dolor sit amet, consectetuer<br>adipiscing elit , sed diam nonummy nibh</p>
    <span class="btn-outline">READ MORE</span>
  </div>
  <div class="svc" style="left:797px">
    <div class="ico"><svg width="96" height="70" viewBox="0 0 96 70" fill="none" stroke="#fff" stroke-width="2.4"><rect x="4" y="8" width="54" height="40"/><path d="M22 48v10M14 60h34M20 20l12 8-12 8z"/><path d="M52 24h12l16-12v36L64 36H52z"/><path d="M86 18l6-4M86 30h8M86 42l6 4"/></svg></div>
    <h3>Marketing New Products</h3>
    <p>Lorem ipsum dolor sit amet, consectetuer<br>adipiscing elit , sed diam nonummy nibh</p>
    <span class="btn-outline">READ MORE</span>
  </div>
</section>

<h2 class="title" style="top:1757px">Latest <em>News</em></h2>
<div class="rule" style="top:1804px"></div>
<span class="abs chev" style="left:58px;top:1924px">‹</span>
<span class="abs chev" style="left:1124px;top:1924px">›</span>
<article class="news" style="left:114px"><span class="tag">JUNE 05, 2019</span><h4>LOREM IPSUM DOLOR SIT AMET NSE</h4><p>Quis nostrud exerci tation ullamcorper suscipit lobortis nisl ut aliquip ex ea commodonsequat Duis autem vel eum iriure</p><a>LEARN MORE</a></article>
<article class="news" style="left:459px"><span class="tag">JUNE 05, 2019</span><h4>SED DIAM NONUMMY NIBH EUISMOD</h4><p>Quis nostrud exerci tation ullamcorper suscipit lobortis nisl ut aliquip ex ea commodonsequat Duis autem vel eum iriure</p><a>LEARN MORE</a></article>
<article class="news" style="left:805px"><span class="tag">JUNE 05, 2019</span><h4>LOREM IPSUM DOLOR SIT AMET NSE</h4><p>Quis nostrud exerci tation ullamcorper suscipit lobortis nisl ut aliquip ex ea commodonsequat Duis autem vel eum iriure</p><a>LEARN MORE</a></article>

<section class="abs cta" role="img" aria-label="Dark photo of a scientist working at a microscope">
  <h2>Not Sure of Your Next Step?</h2>
  <p>Lorem ipsum dolor sit amet, consectetuer adipiscing elit, sed<br>nonummy nibh euismod tincidunt ut laoreet dolore</p>
  <div class="go">GET STARTED</div>
</section>

<h2 class="title" style="top:2458px">Our <em>Partners</em></h2>
<div class="rule" style="top:2504px"></div>
<svg class="abs" style="left:48px;top:2552px" width="22" height="40" viewBox="0 0 22 40"><path d="M20 2 3 20l17 18" fill="none" stroke="#bbb" stroke-width="2"/></svg>
<svg class="abs" style="left:1116px;top:2552px" width="22" height="40" viewBox="0 0 22 40"><path d="M2 2l17 18L2 38" fill="none" stroke="#999" stroke-width="2"/></svg>
<div class="partner active" style="left:113px"><i></i>Kelvra Bio</div>
<div class="partner" style="left:280px"><i></i>Nuvix</div>
<div class="partner" style="left:446px"><i></i>Orbalis</div>
<div class="partner" style="left:613px"><i></i>Tessaro</div>
<div class="partner" style="left:779px"><i></i>Coralyn</div>
<div class="partner" style="left:946px"><i></i>Pellion Lab</div>

<footer class="abs footer">
  <h5 style="left:115px">Quick Links</h5><div class="ul" style="left:139px"></div>
  <ul class="links abs" style="left:113px;top:112px">
    <li>Home</li><li>About Us</li><li>Services</li><li>Contact Us</li>
  </ul>
  <div class="vsep" style="left:269px"></div>

  <h5 style="left:325px">Contact Details</h5><div class="ul" style="left:368px"></div>
  <div class="contact-row" style="top:112px"><svg width="12" height="16" viewBox="0 0 12 16"><path d="M6 15S1 9 1 6a5 5 0 0 1 10 0c0 3-5 9-5 9z" fill="var(--blue)"/><circle cx="6" cy="6" r="2" fill="#121314"/></svg><span>123 Loren Ipsum dolor mnwp<br>AB Mnwrr Conr 1234</span></div>
  <div class="contact-row" style="top:170px"><svg width="14" height="14" viewBox="0 0 14 14"><path d="M3 1l3 3-2 2c1 2 2 3 4 4l2-2 3 3-2 2C5 13 1 9 1 3z" fill="var(--blue)"/></svg><span>215-555-0147</span></div>
  <div class="contact-row" style="top:214px"><svg width="15" height="11" viewBox="0 0 15 11"><rect width="15" height="11" fill="var(--blue)"/><path d="m0 0 7.5 6L15 0" fill="none" stroke="#121314" stroke-width="1.3"/></svg><span>info@veranteldx.com</span></div>
  <div class="vsep" style="left:583px"></div>

  <h5 style="left:639px">Quick Inquiry</h5><div class="ul" style="left:679px"></div>
  <div class="field" style="top:112px">Name</div>
  <div class="field" style="top:148px">Email</div>
  <div class="field" style="top:184px">Message</div>
  <div class="submit">Submit</div>
  <div class="vsep" style="left:921px"></div>

  <h5 style="left:977px">Follow Us</h5><div class="ul" style="left:1020px"></div>
  <div class="social" style="top:124px"><i></i>COMMONS</div>
  <div class="social" style="top:170px"><i></i>CHIRPLINE</div>
  <div class="social" style="top:216px"><i></i>WORKFOLD</div>
</footer>
<div class="abs copy">Copyright © 2019 Verantel Dx . All Rights Reserved.</div>

</body>
</html>
```